Design my Display Ad! Product for Muscle Cramps -- Need Your Talent!

I need the PSD of a square display ad to be the design concept for other ad formats. The product is for leg and muscle cramps. The ad needs to encourage clicks, not simply impressions. Image should contain legs.

Visit www.sorelvanta.com for a better idea of the product.

Target Market(s)

People age 55+ with leg cramps

Industry/Entity Type

Health And Wellness

Font styles to use
Sans Serif

Colors

Designer to choose colors to be used in the design.

Requirements
Must have
• One version with the text:
• The Real Cause of Leg Cramps
• Discover the Secret
• The other version with the text:
• Leg Cramps at Night
• Discover the Real Cause
• An image focused on legs.
• Attractive presentation -- this is a premium organic brand.
• Visit www.sorelvanta.com for a better understanding of the product

```html
<!DOCTYPE html>
<html lang="en">
<head>
<meta charset="utf-8">
<title>Sorelvanta Display Ads</title>
<link href="https://fonts.googleapis.com/css2?family=Open+Sans:wght@400;600;700&display=swap" rel="stylesheet">
<style>
  :root {
    --brand-blue: #27a9e1;
    --cta-green: #7ea70a;
    --ink: #2f2f2f;
    --white: #ffffff;
    --skin-light: #f3d9c6;
    --skin-mid: #e2b193;
    --canvas: #ffffff;
  }
  * { box-sizing: border-box; margin: 0; padding: 0; }
  html, body { width: 1200px; height: 1200px; overflow: hidden; background: var(--canvas); }
  body { position: relative; font-family: "Open Sans", sans-serif; }

  .ad { position: absolute; background: var(--white); border: 1px solid var(--brand-blue); overflow: hidden; }
  .ad__art { position: absolute; inset: 0; width: 100%; height: 100%; }
  .ad__text { position: absolute; text-align: center; color: var(--white); }
  .headline-strong { font-weight: 700; display: block; }
  .headline-light { font-weight: 400; display: block; }
  .subline { color: var(--ink); font-weight: 600; }

  .brand-name { position: absolute; color: var(--brand-blue); font-weight: 700; text-align: center; letter-spacing: 0.5px; }

  .cta {
    position: absolute; background: var(--cta-green); color: var(--white);
    font-weight: 700; display: flex; align-items: center; justify-content: center; gap: 4px;
    text-transform: uppercase; white-space: nowrap;
  }
  .cta svg { flex: none; }

  /* 160 x 600 */
  .ad--sky { left: 115px; top: 206px; width: 160px; height: 600px; }
  .ad--sky .brand-name { left: 0; width: 160px; top: 20px; font-size: 24px; }
  .ad--sky .ad__text { left: 0; width: 160px; top: 300px; }
  .ad--sky .headline-strong { font-size: 34px; line-height: 44px; }
  .ad--sky .headline-light { font-size: 29px; line-height: 36px; }
  .ad--sky .subline { font-size: 17px; line-height: 22px; margin-top: 20px; display: block; }
  .ad--sky .cta { left: 8px; top: 547px; width: 143px; height: 42px; font-size: 16px; }

  /* 300 x 600 */
  .ad--half { left: 333px; top: 205px; width: 300px; height: 600px; }
  .ad--half .brand-name { left: 0; width: 300px; top: 26px; font-size: 38px; }
  .ad--half .ad__text { left: 0; width: 300px; top: 358px; }
  .ad--half .headline-strong { font-size: 45px; line-height: 54px; }
  .ad--half .headline-light { font-size: 36px; line-height: 42px; }
  .ad--half .subline { font-size: 19px; margin-top: 16px; display: block; }
  .ad--half .cta { left: 55px; top: 549px; width: 177px; height: 43px; font-size: 20px; }

  /* 300 x 250 */
  .ad--rect { left: 674px; top: 208px; width: 300px; height: 250px; }
  .ad--rect .ad__text { left: 150px; width: 150px; top: 16px; }
  .ad--rect .headline-strong { font-size: 26px; line-height: 35px; }
  .ad--rect .headline-light { font-size: 26px; line-height: 35px; }
  .ad--rect .subline { font-size: 17px; line-height: 22px; margin-top: 6px; display: block; }
  .ad--rect .brand-name { left: 4px; width: 140px; top: 198px; font-size: 24px; text-align: left; }
  .ad--rect .cta { left: 151px; top: 202px; width: 143px; height: 42px; font-size: 16px; }

  /* 728 x 90 */
  .ad--leader { left: 115px; top: 836px; width: 728px; height: 90px; }
  .ad--leader .ad__text { left: 240px; width: 330px; top: 4px; }
  .ad--leader .headline-row { font-size: 32px; line-height: 44px; white-space: nowrap; }
  .ad--leader .headline-row b { font-weight: 700; }
  .ad--leader .headline-row span { font-weight: 400; }
  .ad--leader .subline { font-size: 16px; display: block; margin-top: 5px; }
  .ad--leader .brand-name { left: 575px; width: 143px; top: 6px; font-size: 20px; }
  .ad--leader .cta { left: 574px; top: 42px; width: 143px; height: 42px; font-size: 18px; }
</style>
</head>
<body>

<!-- 160 x 600 skyscraper -->
<section class="ad ad--sky">
  <svg class="ad__art" viewBox="0 0 160 600" aria-hidden="false">
    <defs>
      <linearGradient id="skinSky" x1="0" y1="0" x2="1" y2="1">
        <stop offset="0" stop-color="#f6e2d3"/><stop offset="1" stop-color="#dca786"/>
      </linearGradient>
    </defs>
    <rect x="0" y="72" width="160" height="190" fill="url(#skinSky)" role="img" aria-label="Photo of a woman holding her calf while bending her leg"/>
    <polygon points="0,290 160,249 160,540 0,540" fill="var(--brand-blue)"/>
  </svg>
  <div class="brand-name">Sorelvanta</div>
  <div class="ad__text">
    <span class="headline-strong">Leg<br>Cramps</span>
    <span class="headline-light">at Night</span>
    <span class="subline">Discover the Real Cause</span>
  </div>
  <a class="cta">Learn More <svg width="16" height="14" viewBox="0 0 16 14"><path d="M2 1l6 6-6 6M8 1l6 6-6 6" fill="none" stroke="#fff" stroke-width="2"/></svg></a>
</section>

<!-- 300 x 600 half page -->
<section class="ad ad--half">
  <svg class="ad__art" viewBox="0 0 300 600">
    <defs>
      <linearGradient id="skinHalf" x1="0" y1="0" x2="1" y2="1">
        <stop offset="0" stop-color="#f6e2d3"/><stop offset="1" stop-color="#dca786"/>
      </linearGradient>
    </defs>
    <rect x="0" y="92" width="300" height="230" fill="url(#skinHalf)" role="img" aria-label="Photo of a woman holding her calf while bending her leg"/>
    <polygon points="0,330 300,260 300,540 0,540" fill="var(--brand-blue)"/>
  </svg>
  <div class="brand-name">Sorelvanta</div>
  <div class="ad__text">
    <span class="headline-strong">Leg Cramps</span>
    <span class="headline-light">at Night</span>
    <span class="subline">Discover the Real Cause</span>
  </div>
  <a class="cta">Learn More <svg width="18" height="16" viewBox="0 0 16 14"><path d="M2 1l6 6-6 6M8 1l6 6-6 6" fill="none" stroke="#fff" stroke-width="2"/></svg></a>
</section>

<!-- 300 x 250 medium rectangle -->
<section class="ad ad--rect">
  <svg class="ad__art" viewBox="0 0 300 250">
    <defs>
      <linearGradient id="skinRect" x1="0" y1="0" x2="1" y2="1">
        <stop offset="0" stop-color="#f6e2d3"/><stop offset="1" stop-color="#dca786"/>
      </linearGradient>
    </defs>
    <rect x="0" y="0" width="160" height="194" fill="url(#skinRect)" role="img" aria-label="Photo of a woman holding her calf while bending her leg"/>
    <polygon points="176,0 300,0 300,194 133,194" fill="var(--brand-blue)"/>
  </svg>
  <div class="ad__text">
    <span class="headline-strong">Leg<br>Cramps</span>
    <span class="headline-light">at Night</span>
    <span class="subline">Discover the<br>Real Cause</span>
  </div>
  <div class="brand-name">Sorelvanta</div>
  <a class="cta">Learn More <svg width="16" height="14" viewBox="0 0 16 14"><path d="M2 1l6 6-6 6M8 1l6 6-6 6" fill="none" stroke="#fff" stroke-width="2"/></svg></a>
</section>

<!-- 728 x 90 leaderboard -->
<section class="ad ad--leader">
  <svg class="ad__art" viewBox="0 0 728 90">
    <defs>
      <linearGradient id="skinLeader" x1="0" y1="0" x2="1" y2="1">
        <stop offset="0" stop-color="#f6e2d3"/><stop offset="1" stop-color="#dca786"/>
      </linearGradient>
    </defs>
    <rect x="0" y="0" width="240" height="90" fill="url(#skinLeader)" role="img" aria-label="Photo of a bent leg with a hand holding the calf"/>
    <polygon points="244,0 568,0 568,90 218,90" fill="var(--brand-blue)"/>
  </svg>
  <div class="ad__text">
    <div class="headline-row"><b>Leg Cramps</b> <span>at Night</span></div>
    <span class="subline">Discover the Real Cause</span>
  </div>
  <div class="brand-name">Sorelvanta</div>
  <a class="cta">Learn More <svg width="17" height="15" viewBox="0 0 16 14"><path d="M2 1l6 6-6 6M8 1l6 6-6 6" fill="none" stroke="#fff" stroke-width="2"/></svg></a>
</section>

</body>
</html>
```